VOR Exterior Coatings

double sided. the front i want the name of the business each word on a new line with the VOR being bigger. id like teal, black and white colors. the back i want my contact info. Flat, no gloss. Something professional and I want to feel the letters bump put of the card. if possible maybe a paint sprayer in corner. not a car paint spray. (no tank on top of gun)
no vehicle paint sprayers. that means no tank on top of the gun. doesn't have to have a sprayer. black/dark background on the front. white back ground on back with info

```html
<!DOCTYPE html>
<html lang="en">
<head>
<meta charset="utf-8">
<title>VOR Exterior Coatings – Business Cards</title>
<link href="https://fonts.googleapis.com/css2?family=Open+Sans:wght@400;700&display=swap" rel="stylesheet">
<style>
  :root {
    --stage: #2b2b2d;
    --card-dark: #050505;
    --card-light: #ffffff;
    --teal: #12a0a6;
    --white: #ffffff;
    --ink: #1a1a1a;
    --ink-soft: #333333;
  }
  html, body {
    margin: 0;
    padding: 0;
    width: 1200px;
    height: 900px;
    overflow: hidden;
    background: var(--stage);
    font-family: "Open Sans", Arial, sans-serif;
  }
  .canvas {
    position: relative;
    width: 1200px;
    height: 900px;
  }
  .card {
    position: absolute;
    width: 700px;
    height: 400px;
    border-radius: 28px;
    box-sizing: border-box;
    overflow: hidden;
  }
  .card--front { left: 60px; top: 50px; background: var(--card-dark); }
  .card--back  { left: 440px; top: 460px; background: var(--card-light); }

  .brand {
    position: absolute;
    left: 0; right: 0;
    margin: 0;
    text-align: center;
    color: var(--teal);
    font-weight: 700;
    text-transform: uppercase;
    line-height: 1;
  }
  .brand__main { display: block; }
  .brand__word { display: block; }

  /* Front */
  .card--front .brand { top: 72px; }
  .card--front .brand__main { font-size: 120px; letter-spacing: 8px; }
  .card--front .brand__word { font-size: 42px; letter-spacing: 4px; margin-top: 12px; }

  /* Back */
  .card--back .brand { top: 30px; }
  .card--back .brand__main { font-size: 72px; letter-spacing: 5px; }
  .card--back .brand__word { font-size: 24px; letter-spacing: 3px; margin-top: 6px; }

  .details {
    position: absolute;
    left: 0; right: 0;
    top: 200px;
    display: flex;
    justify-content: center;
    align-items: center;
    gap: 26px;
  }
  .person { text-align: right; }
  .person__name {
    color: var(--teal);
    font-weight: 700;
    font-size: 28px;
    letter-spacing: 1px;
    text-transform: uppercase;
    line-height: 1.1;
  }
  .person__role {
    color: var(--ink);
    font-size: 20px;
    line-height: 1.3;
  }
  .divider {
    width: 2px;
    height: 84px;
    background: var(--ink);
  }
  .contact { list-style: none; margin: 0; padding: 0; }
  .contact__item {
    display: flex;
    align-items: center;
    gap: 12px;
    color: var(--ink-soft);
    font-size: 19px;
    line-height: 28px;
  }
  .contact__icon { width: 18px; height: 18px; fill: var(--teal); flex: none; }
  .address {
    position: absolute;
    left: 0; right: 0;
    bottom: 30px;
    margin: 0;
    text-align: center;
    color: var(--ink);
    font-size: 20px;
    letter-spacing: 0.5px;
  }
</style>
</head>
<body>
<main class="canvas">

  <section class="card card--front" aria-label="Business card front">
    <h1 class="brand">
      <span class="brand__main">VOR</span>
      <span class="brand__word">Exterior</span>
      <span class="brand__word">Coatings</span>
    </h1>
  </section>

  <section class="card card--back" aria-label="Business card back">
    <div class="brand">
      <span class="brand__main">VOR</span>
      <span class="brand__word">Exterior</span>
      <span class="brand__word">Coatings</span>
    </div>

    <div class="details">
      <div class="person">
        <div class="person__name">Daniel Reeves</div>
        <div class="person__role">Manager</div>
      </div>
      <div class="divider"></div>
      <ul class="contact">
        <li class="contact__item">
          <svg class="contact__icon" viewBox="0 0 24 24" aria-hidden="true"><path d="M6.6 10.8a15.1 15.1 0 0 0 6.6 6.6l2.2-2.2a1 1 0 0 1 1-.25 11.4 11.4 0 0 0 3.6.57 1 1 0 0 1 1 1V20a1 1 0 0 1-1 1A17 17 0 0 1 3 4a1 1 0 0 1 1-1h3.5a1 1 0 0 1 1 1c0 1.25.2 2.45.57 3.57a1 1 0 0 1-.25 1z"/></svg>
          555-014-2100
        </li>
        <li class="contact__item">
          <svg class="contact__icon" viewBox="0 0 24 24" aria-hidden="true"><path d="M2 5h20v14H2z M4 7v.5l8 5.5 8-5.5V7l-8 5.5z" fill-rule="evenodd"/></svg>
          hello@vormail.com
        </li>
        <li class="contact__item">
          <svg class="contact__icon" viewBox="0 0 24 24" aria-hidden="true"><circle cx="12" cy="12" r="10"/><circle cx="12" cy="12" r="4" fill="#ffffff"/></svg>
          www.vorcoatings.com
        </li>
      </ul>
    </div>

    <p class="address">Your address, city, state, ZIP 0000</p>
  </section>

</main>
</body>
</html>
```